GJ & DW Fencing Pty Ltd

We already have an existing logo created by Pixel Harbour however we have restructured to a company. We would like someone to add Pty Ltd to our business name please.

Colors

Designer to choose only greyscale colors for use in the design.

```html
<!DOCTYPE html>
<html lang="en">
<head>
<meta charset="utf-8">
<title>GJ &amp; DW Fencing Pty Ltd – Business Card</title>
<link rel="stylesheet" href="https://fonts.googleapis.com/css2?family=Lora:wght@400;700&display=swap">
<style>
  :root {
    --bg: #2b2b2d;
    --card-dark: #151516;
    --card-light: #ffffff;
    --ink: #1a1a1a;
    --ink-soft: #3a3a3a;
    --emboss: #5c5c5e;
    --rule: #1a1a1a;
  }
  * { margin: 0; padding: 0; box-sizing: border-box; }
  html, body { width: 1200px; height: 800px; overflow: hidden; }
  body {
    background: var(--bg);
    font-family: "Lora", Georgia, serif;
    position: relative;
  }
  .card {
    position: absolute;
    top: 250px;
    width: 520px;
    height: 300px;
    border-radius: 18px;
  }
  .card--front { left: 50px; background: var(--card-dark); }
  .card--back { left: 630px; background: var(--card-light); color: var(--ink); }

  .brand {
    display: flex;
    align-items: center;
    gap: 10px;
    font-weight: 700;
    white-space: nowrap;
  }
  .brand__dot {
    width: 14px; height: 14px; border-radius: 50%;
    background: currentColor;
  }
  .card--front .brand {
    position: absolute;
    left: 50%; top: 50%;
    transform: translate(-50%, -50%);
    font-size: 30px;
    color: var(--emboss);
  }
  .card--back .brand {
    position: absolute;
    left: 150px; top: 52px;
    font-size: 26px;
    color: var(--ink);
  }
  .rule-top {
    position: absolute;
    left: 240px; right: 30px; top: 120px;
    height: 2px; background: var(--rule);
  }
  .company {
    position: absolute;
    right: 30px; top: 132px;
    text-align: right;
    font-size: 13px;
    line-height: 1.5;
  }
  .company__name { font-weight: 700; }
  .person {
    position: absolute;
    left: 30px; top: 196px;
  }
  .person__name { font-weight: 700; font-size: 15px; letter-spacing: 0.5px; }
  .person__role { font-size: 13px; color: var(--ink-soft); }
  .rule-name {
    position: absolute;
    left: 170px; right: 300px; top: 206px;
    height: 2px; background: var(--rule);
  }
  .contacts {
    position: absolute;
    left: 30px; top: 244px;
    list-style: none;
    font-size: 13px;
    line-height: 1.6;
  }
  .contacts li { display: flex; align-items: center; gap: 8px; }
  .contacts svg { width: 16px; height: 16px; flex: none; }
</style>
</head>
<body>
  <section class="card card--front" aria-label="Card front">
    <div class="brand"><span class="brand__dot"></span>GJ &amp; DW Fencing Pty Ltd</div>
  </section>

  <section class="card card--back" aria-label="Card back">
    <div class="brand"><span class="brand__dot"></span>GJ &amp; DW Fencing Pty Ltd</div>
    <div class="rule-top"></div>
    <div class="company">
      <div class="company__name">GJ &amp; DW Fencing Pty Ltd</div>
      <div>PO Box 418 Greenvale WA 6120</div>
    </div>
    <div class="person">
      <div class="person__name">LEWIS CARTER</div>
      <div class="person__role">President</div>
    </div>
    <div class="rule-name"></div>
    <ul class="contacts">
      <li>
        <svg viewBox="0 0 16 16" aria-hidden="true"><circle cx="8" cy="8" r="8" fill="#1a1a1a"/><rect x="5.5" y="4" width="5" height="8" rx="1" fill="none" stroke="#fff" stroke-width="1.2"/></svg>
        Ray 0400 118 275
      </li>
      <li>
        <svg viewBox="0 0 16 16" aria-hidden="true"><circle cx="8" cy="8" r="8" fill="#1a1a1a"/><rect x="4" y="5" width="8" height="6" fill="#fff"/><path d="M4 5l4 3.5L12 5" fill="none" stroke="#1a1a1a" stroke-width="1"/></svg>
        gjdwfencing@mailbox.net
      </li>
    </ul>
  </section>
</body>
</html>
```